Tech business card design

We need an amazing business card design for our new business 'Pexla' a marketing tech startup based in Sydney, Australia. We provide an online marketplace for businesses to search and buy advertising media, connect with service providers and learn more about marketing. We wish to communicate 'cool tech', reliability and professionalism and design based around our logo.

Target Market(s)

Business Owners

Contact Information for Business Card

Name
Position
Email Address
Website
Phone Number

Font styles to use
Other font styles liked:
• Avenir & Avenir Next

Colors

Designer to choose colors to be used in the design.

```html
<!DOCTYPE html>
<html lang="en">
<head>
<meta charset="utf-8">
<title>Pexla Business Card</title>
<link href="https://fonts.googleapis.com/css2?family=Lato:wght@400;700;900&display=swap" rel="stylesheet">
<style>
  :root {
    --page: #e9e9eb;
    --card: #fbfbfc;
    --navy: #14163a;
    --text: #3a3a44;
    --rule: #d4d4d8;
  }
  html, body {
    margin: 0;
    width: 1200px;
    height: 900px;
    overflow: hidden;
    background: var(--page);
    font-family: "Lato", sans-serif;
  }
  .card {
    position: absolute;
    left: 180px;
    top: 190px;
    width: 840px;
    height: 520px;
    background: var(--card);
    box-shadow: 0 10px 30px rgba(20, 22, 58, 0.12);
  }
  .brand {
    position: absolute;
    left: 0;
    right: 0;
    top: 95px;
    text-align: center;
    font-weight: 900;
    font-size: 150px;
    line-height: 1;
    color: var(--navy);
    letter-spacing: -2px;
  }
  .brand-rule {
    position: absolute;
    left: 88px;
    width: 665px;
    top: 320px;
    height: 5px;
    background: var(--navy);
  }
  .person {
    position: absolute;
    right: calc(840px - 388px);
    top: 394px;
    text-align: right;
  }
  .person-name {
    font-weight: 900;
    font-size: 27px;
    letter-spacing: 1px;
    color: var(--navy);
    line-height: 1.15;
  }
  .person-role {
    font-size: 23px;
    color: var(--text);
    line-height: 1.15;
  }
  .divider {
    position: absolute;
    left: 421px;
    top: 376px;
    width: 1px;
    height: 80px;
    background: var(--rule);
  }
  .contacts {
    position: absolute;
    left: 448px;
    top: 370px;
    margin: 0;
    padding: 0;
    list-style: none;
  }
  .contacts li {
    display: flex;
    align-items: center;
    height: 31px;
    font-size: 23px;
    color: var(--text);
  }
  .contacts svg {
    width: 19px;
    height: 19px;
    margin-right: 9px;
    fill: var(--text);
  }
</style>
</head>
<body>
  <div class="card">
    <div class="brand">pexla</div>
    <div class="brand-rule"></div>

    <div class="person">
      <div class="person-name">MARCUS REID</div>
      <div class="person-role">Managing Director</div>
    </div>

    <div class="divider"></div>

    <ul class="contacts">
      <li>
        <svg viewBox="0 0 20 20" aria-hidden="true"><path d="M2 7c0-2 3-4 8-4s8 2 8 4v1h-4V6.5H6V8H2z"/><path d="M5 10h10l2 7H3z"/></svg>
        044-987 654 321
      </li>
      <li>
        <svg viewBox="0 0 20 20" aria-hidden="true"><path d="M2 4h16v12H2z M3.5 5.5v.4L10 11l6.5-5.1v-.4z M3.5 7.8v6.7h13V7.8L10 12.9z" fill-rule="evenodd"/></svg>
        hello@pexlamail.com
      </li>
      <li>
        <svg viewBox="0 0 20 20" aria-hidden="true"><circle cx="10" cy="10" r="8"/><path d="M6 6c2 0 2 2 4 2s1 3-1 3-2 3-4 2l-1-4z M12 12c1 0 3 0 3 2l-2 2-1-2z" fill="#fbfbfc"/></svg>
        www.pexlasite.com
      </li>
    </ul>
  </div>
</body>
</html>
```